Marava Cove Lodge Christmas wishes 2013

We require postcards designed to mail our to our clients for Christmas. We are a SURF travel company, with a high end market and like to mail our Christmas postcards to all our guests that have stayed with us through the year. Front cover will have images and text (ie Seasons Greeting) and our logo. The back will have space for TO: name & address and postage stamp. Will also have some basic text (ie The Management & Staff at Marava Cove Lodge wish you and your family all the best for the Festive Season and New Year. We look forward to seeing you back at Marava Cove Lodge again soon etc etc). Here is link to main image https://www.filecrate-example.com/sh/qwmxrtz481plo/Vb7kRtPwqN

Target Market(s)

Our clients are mostly mature men (40-70) surfers who purchase luxury surf trips

Industry/Entity Type

Travel

Requirements
Must have
• Ocean Image (front)
Logo x 2 in same colour - Orindel & Marava Cove Lodge (front)
Text (front)
Back to be white
Space for name & address (back)
Space for postage stamp (back)
Message (back)
Website www.orindellodges-example.com (back)

```html
<!DOCTYPE html>
<html lang="en">
<head>
<meta charset="utf-8">
<title>Marava Cove Lodge – Season's Greetings Postcard</title>
<link rel="stylesheet" href="https://fonts.googleapis.com/css2?family=Questrial&family=Montserrat:wght@600;700&display=swap">
<style>
  :root {
    --backdrop: #ece9e4;
    --card-white: #ffffff;
    --ink-grey: #8d8d8d;
    --web-grey: #a3a3a3;
    --rule-grey: #b9b9b9;
    --headline-white: #ffffff;
    --sky-light: #8cc3ee;
    --sky-deep: #2f78cf;
    --sea-horizon: #1d63b8;
    --sea-mid: #1a5fa8;
    --sea-deep: #123f7c;
  }
  * { margin: 0; padding: 0; box-sizing: border-box; }
  html, body { width: 1200px; height: 1000px; overflow: hidden; }
  body {
    position: relative;
    background: var(--backdrop);
    font-family: "Questrial", sans-serif;
  }

  .postcard { position: absolute; background: var(--card-white); }

  /* Front */
  .postcard-front { left: 321px; top: 58px; width: 566px; height: 377px; overflow: hidden; }
  .ocean-photo {
    position: absolute; inset: 0;
    background: linear-gradient(180deg,
      var(--sky-light) 0%, var(--sky-deep) 22%, var(--sea-horizon) 28%,
      var(--sea-mid) 55%, var(--sea-deep) 100%);
  }
  .front-headline {
    position: absolute; left: 57px; top: 94px;
    font-family: "Montserrat", sans-serif; font-weight: 700;
    font-size: 17px; letter-spacing: 1.2px;
    color: var(--headline-white);
  }
  .lodge-mark {
    position: absolute; left: 110px; top: 330px; width: 130px;
    text-align: center; color: var(--headline-white);
    font-size: 11px; line-height: 13px;
  }
  .group-mark {
    position: absolute; left: 254px; top: 324px;
    display: flex; align-items: center; gap: 10px;
    color: var(--headline-white);
    font-size: 11px; letter-spacing: 1.6px;
  }
  .group-mark .dot { width: 12px; height: 12px; border-radius: 50%; background: var(--headline-white); }

  /* Back */
  .postcard-back { left: 325px; top: 490px; width: 562px; height: 375px; }
  .greeting-message {
    position: absolute; left: 30px; top: 110px; width: 230px;
    font-size: 13.2px; line-height: 17.5px; letter-spacing: 0.3px;
    color: var(--ink-grey); text-align: justify;
  }
  .greeting-message p + p { margin-top: 17px; }
  .website {
    position: absolute; left: 20px; top: 328px; width: 250px; text-align: center;
    font-family: "Montserrat", sans-serif; font-weight: 600;
    font-size: 12px; color: var(--web-grey);
  }
  .divider { position: absolute; left: 283px; top: 22px; width: 1px; height: 333px; background: var(--rule-grey); }
  .stamp-box {
    position: absolute; left: 489px; top: 20px; width: 44px; height: 71px;
    border: 2px dotted #c9c9c9; padding: 2px;
  }
  .stamp-box span { display: block; width: 100%; height: 100%; border: 1px solid #d4d4d4; }
  .address-lines { position: absolute; left: 316px; top: 189px; width: 209px; }
  .address-lines span { display: block; height: 30px; border-bottom: 1px solid var(--rule-grey); }
  .address-lines span:first-child { height: 0; }
</style>
</head>
<body>
  <section class="postcard postcard-front">
    <div class="ocean-photo" role="img" aria-label="Photograph of a clear blue tropical ocean with a surf break on the horizon and a swimmer in the foreground"></div>
    <h1 class="front-headline">SEASON’S GREETINGS!</h1>
    <div class="lodge-mark">maravacovelodge-example.com</div>
    <div class="group-mark"><span class="dot"></span><span>ORINDEL LODGES &amp; RESORTS</span></div>
  </section>

  <section class="postcard postcard-back">
    <div class="greeting-message">
      <p>The Management &amp; Staff at Marava Cove Lodge wish you and your family all the best for the Festive Season and New Year.</p>
      <p>We look forward to seeing you back at Marava Cove Lodge again soon!</p>
    </div>
    <div class="website">WWW.ORINDELLODGES-EXAMPLE.COM</div>
    <div class="divider"></div>
    <div class="stamp-box"><span></span></div>
    <div class="address-lines"><span></span><span></span><span></span><span></span></div>
  </section>
</body>
</html>
```